Tuition Center Website

We need a new web site for a tutoring company based in sydney.

We only teach senior highschool students and pride ourselves on building the students abilities to think their way through life.

I would like a bright and vibrant website that looks professional and modern.
It needs to look simple and neat but also have the functionality we need.
Images and flash would be good.

Please keep in mind that the site must be appealing to a younger audience.

We need a multipage website with the following navigation bars:

1.Home (As logo not "home" button)
I would like a news box/ticker somewhere that can stream our chatterbook and pipstream feeds and also any news updates we want to put up.
Subscribe to newsletter button.

2. About us.
This needs to be a pull down into:
-What we do
-Why we do it
-How we do it

3. Courses
Pulldown into:
-Maths
-English
-Science
(we may need to attach extra pages behind these e.g. Courses/Science/Physics or Courses/Science/Chemistry and possibly add a link to a new zandlo form)

4. Inspired
This page is like a blog page where we can upload videos, links to articles that we find to be inspiring and hopefully will inspire others.

5. Inspire
This is a recruitment page. Only content here.

6. Contact us.
Mapquill map widget and a 'contact us' form

* Our branding requires green close to #12FF3D

***Please have a look at the current website.
@ www.velmorlearning.com.au

Thanks everybody hope the revision of my brief is better and more informative than my last one

Target Market(s)

senior highschool students aged 15-19, parents ( to a lesser degree)

Industry/Entity Type

It Company

Requirements
Must have
• Ability to change content on pages.

The green doesn't have to be everywhere, but it must be obvious that it is our colour.

Nice to have
• Sites with a nicer mix of images and flash will be given more consideration. But then again, if you amaze us, you amaze us and we will go with your design.
Should not have
• Should stay away from ocre, brown colours and serif fonts.

```html
<!DOCTYPE html>
<html lang="en">
<head>
<meta charset="utf-8">
<title>Velmor Learning</title>
<link href="https://fonts.googleapis.com/css2?family=Cabin:wght@400;500;600&family=Open+Sans:wght@300;400;600;700&display=swap" rel="stylesheet">
<style>
:root{
  --green:#8dc63f;
  --green-hero:#95c93d;
  --green-dark:#6aa32a;
  --ink:#222;
  --text:#555;
  --muted:#777;
  --dark:#1e1e1e;
  --grey-band:#efefef;
  --line:#cfcfcf;
  --white:#fff;
}
*{margin:0;padding:0;box-sizing:border-box}
html,body{width:870px;height:1200px;overflow:hidden;background:var(--white)}
body{position:relative;font-family:"Open Sans",sans-serif;color:var(--text)}
.abs{position:absolute}
.topline{left:0;top:0;width:870px;height:3px;background:#333}

/* header */
.brand{left:94px;top:14px;display:flex;align-items:center;gap:7px}
.brand-mark{width:14px;height:14px;background:var(--green)}
.brand-name{font-family:"Cabin",sans-serif;font-size:19px;font-weight:500;color:var(--ink);line-height:1}
.nav{left:386px;top:37px;display:flex;align-items:center;font-size:11.5px;color:#444}
.nav a{text-decoration:none;color:#444}
.nav .home{background:#2b2b2b;color:#fff;font-weight:700;width:48px;height:22px;line-height:22px;text-align:center;border-radius:4px;position:relative;margin-right:20px;font-size:11px}
.nav .home::after{content:"";position:absolute;left:20px;bottom:-4px;border:4px solid transparent;border-bottom:0;border-top-color:#2b2b2b}
.nav .item{margin-right:29px}

/* hero */
.hero{left:0;top:86px;width:870px;height:316px}
.hero-title{left:106px;top:122px;font-family:"Cabin",sans-serif;font-size:43px;font-weight:400;color:#111;line-height:1}
.hero-sub{left:106px;top:168px;font-family:"Cabin",sans-serif;font-size:21px;color:#111}
.hero-copy{left:106px;top:201px;width:340px;font-family:"Cabin",sans-serif;font-size:11.3px;line-height:16px;color:#fff}
.btn-dark{left:106px;top:276px;width:94px;height:33px;background:#1c1c1c;color:#fff;font-family:"Cabin",sans-serif;font-size:14px;border-radius:3px;display:flex;align-items:center;justify-content:center;box-shadow:0 1px 2px rgba(0,0,0,.4)}
.hero-art{left:524px;top:100px;width:196px;height:240px;border-radius:14px;background:radial-gradient(circle at 50% 40%,#b4db6c,#9bcb48 70%)}
.dots{left:394px;top:357px;display:flex;gap:3px}
.dots span{width:8px;height:8px;border-radius:50%;background:#2a2a2a}
.dots span.on{background:#fff}

/* welcome */
.h2{font-size:15px;color:#333;font-weight:400}
.h2 em{font-style:normal;color:var(--green)}
.welcome-h{left:88px;top:433px}
.welcome-img{left:89px;top:458px;width:180px;height:128px;border:2px solid #fff;box-shadow:0 2px 4px rgba(0,0,0,.25);background:linear-gradient(135deg,#d7c2a6,#9b8a78 60%,#efe6dc)}
.welcome-copy{left:282px;top:457px;width:260px;font-size:8.8px;line-height:11.5px;color:var(--muted)}
.sub-h{left:282px;top:508px;font-size:10.5px;color:#333}
.welcome-more{left:282px;top:515px;width:260px;top:524px;font-size:8.8px;line-height:11.5px;color:var(--muted)}
.read-more{font-size:8.5px;font-weight:700;color:#222;display:flex;align-items:center;gap:4px}
.welcome-read{left:282px;top:578px}

/* trial */
.trial{left:566px;top:432px;width:216px;height:175px;border:2px solid #bdbdbd;background:repeating-linear-gradient(0deg,#fff 0,#fff 2px,#f3f7ec 2px,#f3f7ec 3px);padding:4px}
.trial-in{width:100%;height:100%;background:linear-gradient(#ffffff00,#fff 40%)}
.trial h3{position:absolute;left:15px;top:16px;font-size:20px;font-weight:700;color:#111}
.trial-icon{position:absolute;left:15px;top:64px;width:34px;height:34px;background:var(--green)}
.trial p{position:absolute;left:58px;top:62px;width:150px;font-size:10.3px;line-height:14.5px;color:#222}
.btn-green{background:var(--green);color:#fff;font-weight:600;display:flex;align-items:center;justify-content:center}
.trial .btn-green{position:absolute;left:55px;top:133px;width:112px;height:25px;font-size:10.5px}

/* testimonials */
.say-h{left:88px;top:647px}
.say-rule{left:88px;top:674px;width:434px;border-top:1px dashed #bbb}
.quotes{left:89px;top:685px;width:450px;font-size:8.8px;line-height:13px;color:var(--muted);font-weight:300}
.quotes p{margin-bottom:13px}
.enquire{left:89px;top:796px;width:96px;height:26px;font-size:11px;border-radius:2px}

/* news */
.news{left:570px;top:648px;width:214px;height:174px;border-bottom:1px dashed #aaa}
.news-icon{position:absolute;left:0;top:0;width:34px;height:28px;background:#ddd;transform:rotate(-12deg);border-radius:2px}
.news h3{position:absolute;left:42px;top:2px;font-size:15px;font-weight:400;color:#333}
.news h3 em{font-style:normal;color:var(--green)}
.news-rail{position:absolute;right:2px;top:22px;height:145px;border-left:1px dashed #888}
.news-thumb{position:absolute;right:0;top:50px;width:5px;height:20px;background:var(--green);border-radius:3px}
.news-item{position:absolute;left:6px;width:190px}
.news-item .brace{position:absolute;left:0;top:-2px;font-size:30px;line-height:30px;color:var(--green-dark);font-weight:300}
.news-item p{margin-left:17px;font-size:8.6px;line-height:11.3px;color:var(--text)}
.news-item .date{text-align:right;font-size:8px;font-weight:700;color:#222;margin-top:4px}
.news .read-more{position:absolute;left:30px;top:154px}

/* follow band */
.follow{left:0;top:851px;width:870px;height:71px;background:var(--grey-band);border-bottom:2px solid #d7e9bd}
.follow-circle{position:absolute;left:210px;top:16px;width:40px;height:40px;border-radius:50%;border:2px solid #c8c8c8;background:#f7f7f7}
.follow p{position:absolute;left:262px;top:25px;font-size:14px;font-weight:600;color:#444}
.follow p em{font-style:normal;color:var(--green)}
.notch{left:429px;top:922px;border:6px solid transparent;border-bottom:0;border-top-color:var(--green)}

/* footer */
.fcol{top:946px}
.fcol h4{font-size:13px;font-weight:400;color:#222;text-align:center;padding-bottom:9px;border-bottom:1px solid #ccc}
.fcol.contact{left:94px;width:217px}
.fcol.blog{left:334px;width:217px}
.fcol.news-letter{left:579px;width:198px}
.socials{display:flex;gap:11px;margin-top:15px}
.socials span{width:20px;height:20px;border-radius:50%;background:#bdbdbd}
.fsmall{font-size:9px;line-height:14.5px;color:#333}
.contact .fsmall.intro{margin-top:12px}
.contact .fsmall.addr{margin-top:13px}
.blog-post{margin:15px 14px 0 15px;padding-bottom:7px}
.blog-post + .blog-post{border-top:1px dashed #e0e0e0;padding-top:7px;margin-top:4px}
.news-letter .fsmall{margin-top:14px}
.news-letter label{display:block;font-size:8.5px;color:#333;margin-top:8px}
.news-letter .field{width:160px;height:23px;border:1px solid #ccc;border-radius:2px;margin-top:3px;background:#fff}
.subscribe{margin-top:10px;width:59px;height:16px;background:#1c1c1c;color:#fff;font-size:8.5px;display:flex;align-items:center;justify-content:center;border-radius:2px}
.copyright{left:0;top:1168px;width:870px;text-align:center;font-size:9.3px;color:#555}
.copyright a{color:var(--green);text-decoration:none}
</style>
</head>
<body>
<div class="abs topline"></div>

<header>
  <div class="abs brand"><span class="brand-mark"></span><span class="brand-name">Velmor Learning</span></div>
  <nav class="abs nav">
    <a class="home">HOME</a>
    <a class="item">About Us</a>
    <a class="item">Courses</a>
    <a class="item">Inspired</a>
    <a class="item">Inspire</a>
    <a>Contact Us</a>
  </nav>
</header>

<section>
  <svg class="abs hero" viewBox="0 0 870 316" width="870" height="316">
    <path d="M0 0H870V240Q690 320 450 316Q200 312 0 240Z" fill="var(--green-hero)"/>
    <g fill="#fff">
      <ellipse cx="205" cy="290" rx="24" ry="14"/>
      <ellipse cx="235" cy="282" rx="28" ry="22"/>
      <ellipse cx="290" cy="280" rx="40" ry="36"/>
      <ellipse cx="340" cy="300" rx="32" ry="22"/>
      <ellipse cx="390" cy="302" rx="30" ry="16"/>
      <ellipse cx="580" cy="290" rx="70" ry="55"/>
      <ellipse cx="650" cy="300" rx="50" ry="30"/>
      <rect x="500" y="302" width="370" height="20"/>
      <rect x="180" y="303" width="230" height="20"/>
    </g>
  </svg>
  <h1 class="abs hero-title">I Am Velmor.</h1>
  <p class="abs hero-sub">real HSC coaching &amp; mentoring.</p>
  <p class="abs hero-copy">The HSC help you need, in the years you need it. We offer small classes, individualised attention and genuine care for each student. It's different - in a good way. Feel free to find out more about us, and let us know if there's any way we can help you on your journey.</p>
  <a class="abs btn-dark">Enquire Now</a>
  <div class="abs hero-art" role="img" aria-label="Illustration of maths formulas, geometry shapes and sticky notes floating above a pair of glasses"></div>
  <div class="abs dots"><span></span><span></span><span class="on"></span><span></span></div>
</section>

<section>
  <h2 class="abs h2 welcome-h">Welcome to <em>Velmor</em></h2>
  <div class="abs welcome-img" role="img" aria-label="Photo of smiling students studying at a desk"></div>
  <p class="abs welcome-copy">Velmor Learning are HSC mentors and tutors who aim to build real relationships and offer you the help you need. HSC tutoring is different at Velmor – in a good way.</p>
  <h3 class="abs sub-h" style="font-weight:400">A Passionate Expertise</h3>
  <p class="abs welcome-more">Lorem Ipsum is simply dummy text of the printing and typesetting industry. Lorem Ipsum has been the industry's standard dummy text ever since the 1500s, when an unknown printer took a galley of type</p>
  <a class="abs read-more welcome-read"><svg width="12" height="8" viewBox="0 0 12 8"><path d="M0 4H11M7 1L11 4L7 7" stroke="#222" fill="none"/></svg>Read More</a>

  <div class="abs trial">
    <div class="trial-in"></div>
    <h3>Free Trial Lesson</h3>
    <div class="trial-icon"></div>
    <p>Because we believe you shouldn't have to sign up until you see what it's actually like. Call or email us now!</p>
    <a class="btn-green">Send an Enquiry</a>
  </div>
</section>

<section>
  <h2 class="abs h2 say-h">What Our Students Say</h2>
  <div class="abs say-rule"></div>
  <div class="abs quotes">
    <p>Velmor is character-building, motivating and more than just a tuition centre. (They) discipline you to study, but it's flexible and enjoyable. They really help you achieve more than you thought you ever could.<br>~Marcus, Northvale Boys HS</p>
    <p>"I like that its an environment I can actually study in; its the only place I can study at without all these distractions!"<br>– Priya, Harbourside Girls High School</p>
  </div>
  <a class="abs btn-green enquire">Enquire Now</a>

  <div class="abs news">
    <div class="news-icon"></div>
    <h3>News <em>Updates</em></h3>
    <div class="news-rail"></div>
    <div class="news-thumb"></div>
    <div class="news-item" style="top:40px"><span class="brace">{</span><p>Lorem Ipsum is simply dummy text of the printing and typesetting industry. Lorem Ipsum has been the industry's</p><p class="date">25-Feb-2013</p></div>
    <div class="news-item" style="top:101px"><span class="brace">{</span><p>Lorem Ipsum is simply dummy text of the printing and typesetting industry. Lorem Ipsum has been the industry's</p><p class="date">25-Feb-2013</p></div>
    <a class="read-more"><svg width="12" height="8" viewBox="0 0 12 8"><path d="M0 4H11M7 1L11 4L7 7" stroke="#222" fill="none"/></svg>Read More</a>
  </div>
</section>

<section class="abs follow">
  <div class="follow-circle"></div>
  <p>Please follow <em>@Velmor Edu</em> for all future updates! 7 days ago</p>
</section>
<div class="abs notch"></div>

<footer>
  <div class="abs fcol contact">
    <h4>Contact Us</h4>
    <div class="socials"><span></span><span></span><span></span><span></span><span></span><span></span><span></span></div>
    <p class="fsmall intro">Get in touch with us to know how we can help you better</p>
    <p class="fsmall addr">Street: 48 Larkspur St Ashfield NSW 2131<br>Phone: (02) 5550 1234<br>Email: learn@velmorlearning.com.au</p>
  </div>
  <div class="abs fcol blog">
    <h4>From Our Blog</h4>
    <div class="blog-post fsmall">Lorem Ipsum is simply dummy text of the printing and typesetting industry. Lorem Ipsum has been the industry.<br>Leon Hart</div>
    <div class="blog-post fsmall">Lorem Ipsum is simply dummy text of the printing and typesetting industry. Lorem Ipsum has been the industry.<br>Owen Pike</div>
  </div>
  <div class="abs fcol news-letter">
    <h4>Newsletters</h4>
    <p class="fsmall">Get , our monthly newsletter, delivered to your inbox each month</p>
    <label>Your Name:</label><div class="field"></div>
    <label style="margin-top:19px">Your E-mail:</label><div class="field"></div>
    <div class="subscribe">Subscribe</div>
  </div>
  <p class="abs copyright"><a>Privacy Policy</a> &nbsp;|&nbsp; Copyright © 2013 - 2013 Velmor Learning</p>
</footer>
</body>
</html>
```